Commercial/Corporate Law Firm needs Website Design

Hi guys. I've started up a new law firm and would love your help designing an attractive website. I'll need both design and coding, and to make it easy for us to edit as necessary later, I think it should be built off a Wordpress.org structure.
FIRST IMPRESSIONS
It's very important that the first impression of the website really captures our prospective clients' attention and impresses them. Their first three seconds needs to be good.
I imagine the homepage may be short, with a menu bar and a compelling image, and with a tagline overlaid or underneath (eg. "It's about results.")
The image should be related to our practice areas: eg. IPOs, corporate transactions, or commercial negotiations.
I have previously suggested there could be a skyline image of Sydney or Adelaide. However, because we are based in Adelaide, I don't think Sydney is appropriate - and Adelaide is probably too boring to use.
HOMEPAGE
Being a new firm, we don't have many existing testimonials, and I will be the only lawyer to start with. So we need to focus on the nature of the services we will provide and how my experience can help them. We have an existing logo to use, and I would like the website colour scheme not to clash with that logo (dark blue and white).
After the initial image and tagline there should be a brief introduction to each of the main areas of work, eg. "We specialise in three main areas of practice:"
1. Corporate Transactions and Regulation
2. Business Law and Dispute Resolution
3. Migration Assistance
These should each have an appropriate photo and link to a separate page that briefly describes our services in that area.
Below that there should be a message from me with a photo. Finally, at the bottom, there should be a "Contact Us" section which shows a Google image of our address, contact details, and then our logo with colours inverted.
OTHER PAGES
While we will need some other pages, they should all be fairly simple. I think we will need one page to say "About Us", where I will put information about my experience. I think we will then need one page for each of the 3 areas listed above, which just needs an appropriate image and then text to describe the service. Finally, a "Contact Us" page which I imagine will be the same as the bottom of the homepage.
OTHER DETAILS
For now you can use details from my LinkedIn page to fill out any other text as necessary, or the photo.
Because the logo is square, I would prefer the design of the website also to be rectangular.
Looking forward to seeing your work! Thank you.
Marcus
Potential clients:
Businesses with legal issues or disputes
Companies wishing to list on the stock market

```html
<!DOCTYPE html>
<html lang="en">
<head>
<meta charset="utf-8">
<title>Corvell Legal — Home</title>
<link rel="stylesheet" href="https://fonts.googleapis.com/css2?family=EB+Garamond:wght@500;600;700&family=Lato:wght@400;700&display=swap">
<style>
  :root{
    --navy:#1b3563;
    --ink:#333a45;
    --muted:#8d8f93;
    --hero-bg:#f3f1ef;
    --panel:#efefef;
    --white:#ffffff;
    --line:#d9d9d9;
  }
  *{box-sizing:border-box;margin:0;padding:0}
  a{text-decoration:none}
  html,body{width:1200px;height:2439px;overflow:hidden;background:var(--white)}
  body{position:relative;font-family:"Lato",Arial,sans-serif;color:var(--muted)}
  .abs{position:absolute}
  .serif{font-family:"EB Garamond",Georgia,serif}

  /* Header */
  .site-header{left:0;top:0;width:1200px;height:156px;background:var(--white)}
  .header-rule{left:0;top:156px;width:1200px;height:5px;background:var(--navy)}
  .brand{display:flex;align-items:center;gap:14px}
  .brand-mark{width:34px;height:34px;background:var(--navy);flex:none}
  .brand-name{font-family:"EB Garamond",Georgia,serif;font-weight:600;color:var(--navy);font-size:34px;line-height:1;white-space:nowrap}
  .search{left:862px;top:31px;width:260px;height:36px;background:#f2f2f2;display:flex;align-items:center;justify-content:space-between;padding:0 14px}
  .search span{font-size:12px;font-style:italic;color:#555}
  .main-nav a{position:absolute;top:102px;font-size:16px;color:#8a8a8a}
  .main-nav a.current{color:var(--navy)}

  /* Hero */
  .hero{left:0;top:161px;width:1200px;height:574px;background:var(--hero-bg)}
  .hero-photo{left:715px;top:161px;width:485px;height:574px;
    background:linear-gradient(100deg,rgba(243,241,239,1) 0%,rgba(214,190,160,.75) 25%,rgba(180,150,120,.8) 55%,rgba(150,95,70,.75) 80%,rgba(220,210,205,.8) 100%)}
  .hero-title{left:78px;top:292px;font-size:66px;font-weight:600;color:var(--navy);letter-spacing:1px;line-height:1}
  .hero-text{left:78px;top:375px;width:610px;font-size:16px;line-height:22px;color:#9a9a9a}

  .btn{position:absolute;display:flex;align-items:center;justify-content:center;background:var(--navy);color:var(--white);
    font-size:22px;font-family:"Lato",Arial,sans-serif;text-decoration:none;border:1px solid var(--navy);box-shadow:0 0 0 3px var(--white),0 0 0 4px var(--navy)}

  /* Practice cards */
  .card{position:absolute;background:var(--white);box-shadow:0 2px 8px rgba(0,0,0,.12);text-align:center}
  .card-photo{position:absolute;left:10px;right:10px}
  .card h3{position:absolute;left:0;right:0;font-family:"EB Garamond",Georgia,serif;font-weight:600;font-size:21px;line-height:24px;color:var(--navy)}
  .card p{position:absolute;left:22px;right:22px;font-size:13px;line-height:21px;color:#9a9a9a}
  .divider{left:360px;top:1074px;width:480px;height:2px;background:linear-gradient(90deg,transparent,#e4e4e4,transparent)}

  /* About */
  .section-title{left:0;width:1200px;text-align:center;font-family:"EB Garamond",Georgia,serif;font-weight:600;font-size:37px;color:var(--navy);letter-spacing:.5px}
  .about-frame{left:78px;top:1216px;width:498px;height:293px;background:var(--white);border:1px solid var(--line);padding:10px}
  .about-photo{width:100%;height:100%;background:linear-gradient(120deg,#2b3142 0%,#3c4257 45%,#5a6378 75%,#2a3043 100%)}
  .about-text{left:598px;top:1229px;width:520px;font-size:16px;line-height:24.4px;color:#8b8b8b}

  /* Contact form */
  .contact{left:0;top:1571px;width:1200px;height:499px;background:var(--panel)}
  .contact-text{left:270px;top:1715px;width:660px;text-align:center;font-size:16px;line-height:24px;color:#9a9a9a}
  .field{position:absolute;border:1px solid var(--navy);background:var(--panel);padding:10px 16px;font-size:13px;color:#b3b3b3}

  /* Footer */
  .footer-heading{font-family:"EB Garamond",Georgia,serif;font-weight:600;font-size:18px;color:var(--navy);letter-spacing:.5px}
  .quick-links a{position:absolute;display:flex;align-items:center;gap:14px;font-size:14px;color:#8a8a8a}
  .quick-links a.current{color:var(--navy)}
  .contact-line{display:flex;align-items:flex-start;gap:14px;font-size:14px;color:#8a8a8a;line-height:22px}
  .social{position:absolute;width:41px;height:41px;border:2px solid var(--navy);background:var(--white)}
  .social.filled{background:var(--navy)}
  .footer-bar{left:0;top:2377px;width:1200px;height:62px;background:var(--navy);display:flex;align-items:center;justify-content:center;color:var(--white);font-size:15px}
  .footer-bar strong{font-family:"EB Garamond",Georgia,serif;font-weight:600;font-size:17px;margin:0 2px 0 6px}
</style>
</head>
<body>

<header class="abs site-header">
  <a class="abs brand" href="#" style="left:78px;top:60px">
    <span class="brand-mark"></span>
    <span class="brand-name">Corvell Legal</span>
  </a>
  <div class="abs search">
    <span>Search here...</span>
    <svg width="16" height="16" viewBox="0 0 16 16"><circle cx="6.5" cy="6.5" r="5" fill="none" stroke="#1b3563" stroke-width="2"/><line x1="10.3" y1="10.3" x2="15" y2="15" stroke="#1b3563" stroke-width="2.4"/></svg>
  </div>
  <nav class="main-nav">
    <a class="current" href="#" style="left:579px">Home</a>
    <a href="#" style="left:702px">About Us</a>
    <a href="#" style="left:852px">Practice Areas</a>
    <a href="#" style="left:1039px">Contact Us</a>
  </nav>
  <svg class="abs" style="left:592px;top:137px" width="20" height="18" viewBox="0 0 20 18">
    <rect x="0" y="0" width="20" height="3" fill="#1b3563"/>
    <rect x="2" y="4" width="3" height="12" fill="#1b3563"/><rect x="8.5" y="4" width="3" height="12" fill="#1b3563"/><rect x="15" y="4" width="3" height="12" fill="#1b3563"/>
  </svg>
</header>
<div class="abs header-rule"></div>

<section>
  <div class="abs hero"></div>
  <div class="abs hero-photo" role="img" aria-label="Two lawyers reviewing documents, overlaid with scales of justice and law books"></div>
  <h1 class="abs serif hero-title">WE GET RESULTS</h1>
  <p class="abs hero-text">Lorem Ipsum is simply dummy text of the printing and typesetting industry. Lorem Ipsum has been the industry's standard dummy.</p>
  <a class="btn" href="#" style="left:80px;top:444px;width:243px;height:55px">GET A FREE QOUTE</a>
</section>

<section>
  <article class="card" style="left:78px;top:637px;width:340px;height:338px">
    <div class="card-photo" role="img" aria-label="Hand signing a contract beside glass office towers" style="top:10px;height:171px;background:linear-gradient(135deg,#7fa6c9,#c9dbe9 50%,#5d7488)"></div>
    <h3 style="top:210px">Corporate Transactions and<br>Regulation</h3>
    <p style="top:268px">Lorem Ipsum is simply dummy text of the printing and typesetting industry. Lorem Ipsum has been the industry's standard dummy.</p>
  </article>
  <article class="card" style="left:782px;top:637px;width:340px;height:338px">
    <div class="card-photo" role="img" aria-label="Colleagues meeting around a table" style="top:10px;height:171px;background:linear-gradient(135deg,#8d8f98,#c4c6cc 50%,#6e6f75)"></div>
    <h3 style="top:210px">Migration Assistance</h3>
    <p style="top:248px">Lorem Ipsum is simply dummy text of the printing and typesetting industry. Lorem Ipsum has been the industry's standard dummy.</p>
  </article>
  <article class="card" style="left:426px;top:595px;width:348px;height:380px">
    <div class="card-photo" role="img" aria-label="Two businessmen in suits in discussion" style="top:10px;height:171px;background:linear-gradient(135deg,#cfe0e4,#e8eef0 45%,#2c3340)"></div>
    <h3 style="top:211px">Business Law and Dispute<br>Resolution</h3>
    <p style="top:270px">Lorem Ipsum is simply dummy text of the printing and typesetting industry. Lorem Ipsum has been the industry's standard dummy.</p>
  </article>
  <a class="btn" href="#" style="left:499px;top:956px;width:201px;height:55px">READ MORE</a>
  <div class="abs divider"></div>
  <svg class="abs" style="left:586px;top:1075px" width="28" height="15" viewBox="0 0 28 15"><polygon points="0,0 28,0 14,14" fill="#ffffff" stroke="#e4e4e4"/><line x1="0" y1="0.5" x2="28" y2="0.5" stroke="#ffffff" stroke-width="2"/></svg>
</section>

<section>
  <h2 class="abs section-title" style="top:1146px">ABOUT CORVELL LEGAL</h2>
  <div class="abs about-frame"><div class="about-photo" role="img" aria-label="Portrait of the firm's principal lawyer in front of a night city skyline"></div></div>
  <p class="abs about-text">Lorem Ipsum is simply dummy text of the printing and typesetting industry. Lorem Ipsum has been the industry's standard dummy text ever since the 1500s, when an unknown printer took a galley of type and scrambled it to make a type specimen book. It has survived not only five centuries, but also the leap into electronic typesetting, remaining essentially unchanged. It was popularised in the 1960s with the release of Letraset sheets containing Lorem Ipsum passages.</p>
  <a class="btn" href="#" style="left:600px;top:1430px;width:201px;height:56px">READ MORE</a>
</section>

<section>
  <div class="abs contact"></div>
  <h2 class="abs section-title" style="top:1643px">KEEP IN TOUCH</h2>
  <p class="abs contact-text">Lorem Ipsum is simply dummy text of the printing and typesetting industry. Lorem Ipsum has been the industry's standard dummy.</p>
  <div class="field" style="left:250px;top:1797px;width:230px;height:45px">Name:</div>
  <div class="field" style="left:489px;top:1797px;width:230px;height:45px">Email:</div>
  <div class="field" style="left:728px;top:1797px;width:230px;height:45px">Phone:</div>
  <div class="field" style="left:250px;top:1854px;width:708px;height:81px">Message:</div>
  <a class="btn" href="#" style="left:498px;top:1948px;width:204px;height:57px">SUBMIT</a>
</section>

<footer>
  <a class="abs brand" href="#" style="left:78px;top:2200px">
    <span class="brand-mark"></span>
    <span class="brand-name">Corvell Legal</span>
  </a>
  <p class="abs" style="left:78px;top:2288px;width:230px;font-size:13px;line-height:22px;color:#8a8a8a">Lorem Ipsum is simply dummy text of the printing and typesetting industry.</p>

  <h4 class="abs footer-heading" style="left:343px;top:2137px">QUICK LINKS</h4>
  <nav class="quick-links">
    <a class="current" href="#" style="left:343px;top:2183px"><svg width="12" height="10" viewBox="0 0 12 10"><polyline points="1,1 5,5 1,9" fill="none" stroke="#1b3563" stroke-width="1.3"/><polyline points="6,1 10,5 6,9" fill="none" stroke="#1b3563" stroke-width="1.3"/></svg>Home</a>
    <a href="#" style="left:343px;top:2219px"><svg width="12" height="10" viewBox="0 0 12 10"><polyline points="1,1 5,5 1,9" fill="none" stroke="#1b3563" stroke-width="1.3"/><polyline points="6,1 10,5 6,9" fill="none" stroke="#1b3563" stroke-width="1.3"/></svg>About Us</a>
    <a href="#" style="left:343px;top:2256px"><svg width="12" height="10" viewBox="0 0 12 10"><polyline points="1,1 5,5 1,9" fill="none" stroke="#1b3563" stroke-width="1.3"/><polyline points="6,1 10,5 6,9" fill="none" stroke="#1b3563" stroke-width="1.3"/></svg>Practice Areas</a>
    <a href="#" style="left:343px;top:2292px"><svg width="12" height="10" viewBox="0 0 12 10"><polyline points="1,1 5,5 1,9" fill="none" stroke="#1b3563" stroke-width="1.3"/><polyline points="6,1 10,5 6,9" fill="none" stroke="#1b3563" stroke-width="1.3"/></svg>Blog</a>
    <a href="#" style="left:343px;top:2328px"><svg width="12" height="10" viewBox="0 0 12 10"><polyline points="1,1 5,5 1,9" fill="none" stroke="#1b3563" stroke-width="1.3"/><polyline points="6,1 10,5 6,9" fill="none" stroke="#1b3563" stroke-width="1.3"/></svg>Contact Us</a>
  </nav>

  <h4 class="abs footer-heading" style="left:564px;top:2137px">CONTACT INFO</h4>
  <div class="abs contact-line" style="left:562px;top:2175px">
    <svg width="18" height="24" viewBox="0 0 18 24"><path d="M9 0C4 0 0 4 0 9c0 6.5 9 15 9 15s9-8.5 9-15c0-5-4-9-9-9z" fill="#1b3563"/><circle cx="9" cy="9" r="3.4" fill="#fff"/></svg>
    <div><div class="serif" style="font-weight:700;color:var(--navy);font-size:15px">CORVELL LEGAL</div>
      <div style="margin-top:6px">123, Lorem Ipsum is simply dummy,<br>City,Country 123456.</div></div>
  </div>
  <div class="abs contact-line" style="left:562px;top:2271px">
    <svg width="18" height="18" viewBox="0 0 24 24"><path d="M6.6 10.8a15.1 15.1 0 0 0 6.6 6.6l2.2-2.2a1 1 0 0 1 1-.25 11.4 11.4 0 0 0 3.6.57 1 1 0 0 1 1 1V20a1 1 0 0 1-1 1A17 17 0 0 1 3 4a1 1 0 0 1 1-1h3.5a1 1 0 0 1 1 1c0 1.25.2 2.45.57 3.6a1 1 0 0 1-.25 1z" fill="#1b3563"/></svg>
    <span>123 456 7878</span>
  </div>
  <div class="abs contact-line" style="left:562px;top:2300px">
    <svg width="18" height="18" viewBox="0 0 24 24" style="margin-top:2px"><rect x="1" y="5" width="22" height="14" fill="#1b3563"/><polyline points="1,5 12,13 23,5" fill="none" stroke="#fff" stroke-width="1.6"/></svg>
    <span>info@corvelllegal.com</span>
  </div>

  <h4 class="abs footer-heading" style="left:875px;top:2137px">FOLLOW US</h4>
  <a class="social filled" href="#" aria-label="Social profile one" style="left:870px;top:2174px"></a>
  <a class="social" href="#" aria-label="Social profile two" style="left:920px;top:2174px"></a>
  <a class="social" href="#" aria-label="Social profile three" style="left:972px;top:2174px"></a>

  <div class="abs footer-bar">©<strong>CORVELL LEGAL</strong>- 2018. All Rights Reserved.</div>
</footer>

</body>
</html>
```